Computer consultant business card

Bexil Software is a newly started computer consulting company. It's a small one-man company that provides mostly Vornix applications but also websites in collaboration with designers. I'm running this company on the side of full time university studies.

I want the final design to be clean and memorable. Be creative! :)

Some inspiration:
http://www.pixelmarta.com/design/48317
http://www.pixelmarta.com/design/2739164/business-card-design-by-frostlynk
http://www.pixelmarta.com/design/604281/business-card-design-by-koralind-vestrabanu

See attachment for my company logo.
Updates

I would like to thank everyone for submitting! I'll need a couple of days to review and ultimately select a design.

Target Market(s)

Non-technical entrepreneurs and small companies.

Industry/Entity Type

University

Requirements
Must have
• My company logo.
In any way, both colors from my logo.
First- and last name, e-mail and phone number.
Double-sided design.
Nice to have
• Something creative with the symbol in my logo

```html
<!DOCTYPE html>
<html lang="en">
<head>
<meta charset="utf-8">
<title>Bexil Software – Business Card</title>
<link rel="stylesheet" href="https://fonts.googleapis.com/css2?family=Saira:wght@400;500;600;700&display=swap">
<style>
  :root {
    --brand-blue: #2a7be4;
    --brand-blue-light: #4a92ec;
    --brand-dark: #333335;
    --card-white: #ffffff;
    --text-dark: #2e2e30;
    --stage: #ececec;
  }
  * { box-sizing: border-box; margin: 0; padding: 0; }
  html, body {
    width: 1200px;
    height: 820px;
    overflow: hidden;
    background: var(--stage);
    font-family: "Saira", "Helvetica Neue", Arial, sans-serif;
  }
  .canvas {
    position: relative;
    width: 1200px;
    height: 820px;
  }
  .card {
    position: absolute;
    width: 560px;
    height: 320px;
    overflow: hidden;
    box-shadow: 0 6px 18px rgba(0,0,0,0.18);
  }

  /* Front side */
  .card-front {
    left: 40px;
    top: 100px;
    background: var(--card-white);
  }
  .front-waves {
    position: absolute;
    inset: 0;
    width: 100%;
    height: 100%;
  }
  .brand {
    position: absolute;
    left: 48px;
    top: 40px;
    display: flex;
    align-items: center;
    gap: 18px;
  }
  .brand-dot {
    width: 74px;
    height: 74px;
    border-radius: 50%;
    background: var(--brand-blue);
  }
  .brand-name {
    font-size: 76px;
    font-weight: 600;
    line-height: 1;
    color: var(--brand-dark);
    letter-spacing: 1px;
  }
  .address {
    position: absolute;
    left: 48px;
    top: 158px;
    font-size: 15px;
    line-height: 20px;
    color: var(--text-dark);
    letter-spacing: 0.3px;
  }
  .contact {
    position: absolute;
    left: 48px;
    top: 194px;
    list-style: none;
    color: var(--text-dark);
  }
  .contact li {
    display: flex;
    align-items: center;
    gap: 7px;
  }
  .contact .phone { font-size: 18px; line-height: 24px; }
  .contact .email { font-size: 15px; line-height: 20px; margin-top: 2px; }
  .contact svg { width: 12px; height: 12px; fill: var(--brand-blue); }
  .person {
    position: absolute;
    right: 28px;
    top: 214px;
    color: var(--card-white);
    line-height: 1.1;
  }
  .person .first-name { font-size: 19px; font-weight: 600; display: block; }
  .person .last-name { font-size: 15px; font-weight: 400; display: block; padding-left: 30px; }

  /* Back side */
  .card-back {
    left: 600px;
    top: 400px;
    background: var(--brand-blue);
  }
  .back-pattern {
    position: absolute;
    inset: 0;
    background: linear-gradient(135deg, var(--brand-blue-light) 0%, var(--brand-blue) 55%, var(--brand-blue-light) 100%);
  }
  .back-wordmark {
    position: absolute;
    inset: 0;
    display: flex;
    align-items: center;
    justify-content: center;
    font-size: 130px;
    font-weight: 600;
    color: var(--card-white);
    letter-spacing: 2px;
  }
</style>
</head>
<body>
<main class="canvas">

  <section class="card card-front" aria-label="Business card front">
    <svg class="front-waves" viewBox="0 0 560 320" preserveAspectRatio="none" aria-hidden="true">
      <path d="M0,272 C160,270 250,252 330,214 C410,176 480,160 560,152 L560,160 C482,168 414,186 336,222 C256,262 162,282 0,284 Z" fill="var(--brand-dark)"/>
      <path d="M200,270 C260,258 300,240 345,218 C420,182 488,166 560,160 L560,166 C490,172 424,188 350,224 C304,246 262,262 200,272 Z" fill="var(--brand-blue)"/>
      <path d="M0,296 C165,294 262,276 345,238 C425,200 490,182 560,176 L560,320 L0,320 Z" fill="var(--brand-blue)"/>
    </svg>

    <div class="brand">
      <span class="brand-dot" aria-hidden="true"></span>
      <span class="brand-name">bexil</span>
    </div>

    <p class="address">00, Complex name, City, State 0042</p>

    <ul class="contact">
      <li class="phone">
        <svg viewBox="0 0 24 24" aria-hidden="true"><path d="M6.6 10.8a15.1 15.1 0 0 0 6.6 6.6l2.2-2.2a1 1 0 0 1 1-.25 11.4 11.4 0 0 0 3.6.57 1 1 0 0 1 1 1V20a1 1 0 0 1-1 1A17 17 0 0 1 3 4a1 1 0 0 1 1-1h3.5a1 1 0 0 1 1 1c0 1.25.2 2.45.57 3.6a1 1 0 0 1-.25 1z"/></svg>
        0461 372859
      </li>
      <li class="email">
        <svg viewBox="0 0 24 24" aria-hidden="true"><path d="M2 6h20v12H2z"/><path d="M3 7l9 6 9-6" fill="none" stroke="#fff" stroke-width="1.6"/></svg>
        info@bexil.com
      </li>
    </ul>

    <p class="person">
      <span class="first-name">First Name</span>
      <span class="last-name">Last Name</span>
    </p>
  </section>

  <section class="card card-back" aria-label="Business card back">
    <div class="back-pattern" role="img" aria-label="Repeating faint pattern of the brand symbol on blue"></div>
    <div class="back-wordmark">bexil</div>
  </section>

</main>
</body>
</html>
```